13 Varno - new website design project

Our company Varno Electrical is developing a new lead generation website focused on Electrical, LED Lighting and Solar Power. We need a high converting website.

Example of our current website is www.varnoelectrical-example.com.au You can take content from this website for this new design. Our colours are red, black and white. For our new website we would like to promote Varno, Spark Every Day. Please listen to the jingle.

The below link is the company jingle that we have developed.
http://www.tunecraftdemo.com.au/vrn-tc-v1/

The key for this brief is to generate leads for Electrical, LED Lighting (for commercial) and Solar Power & Storage.

Target Market(s)

Business owners in Melbourne Victoria

Number of Pages Required

4 page

Colors
ec1f27
ffffff

Requirements
Must have
• This page must be clean, be in line with company branding and a high converting lead website.

```html
<!DOCTYPE html>
<html lang="en">
<head>
<meta charset="utf-8">
<title>Varno Electrical – Spark Every Day</title>
<link href="https://fonts.googleapis.com/css2?family=Roboto:ital,wght@0,300;0,400;0,500;0,700;1,300;1,400&family=Roboto+Condensed:ital,wght@1,400&display=swap" rel="stylesheet">
<style>
:root{
  --red:#ec1f27;
  --red-dark:#c8161d;
  --ink:#222;
  --text:#555;
  --muted:#777;
  --line:#e3e3e3;
  --panel:#f1f1f1;
  --charcoal:#2f3135;
  --footer:#2e3036;
  --white:#fff;
}
*{box-sizing:border-box;margin:0;padding:0}
html,body{width:1200px;height:4196px;overflow:hidden}
body{position:relative;background:var(--white);font-family:'Roboto',Arial,sans-serif;color:var(--text)}
.abs{position:absolute}
.ph{position:absolute}

/* header */
.topline{left:0;top:0;width:1200px;height:6px;background:var(--red)}
.brand{left:78px;top:24px;display:flex;align-items:center;gap:14px}
.brand-dot{width:46px;height:46px;border-radius:50%;background:var(--red)}
.brand-name{font-size:40px;font-weight:700;color:var(--ink);letter-spacing:1px;line-height:1}
.nav{left:288px;top:50px;display:flex;align-items:center;gap:0;width:836px;justify-content:space-between}
.nav a{font-size:16px;color:var(--ink);text-decoration:none;text-transform:uppercase;letter-spacing:.3px}
.nav a.active{background:var(--red);color:var(--white);border-radius:22px;padding:12px 22px}

/* hero */
.hero{left:0;top:126px;width:1200px;height:551px;background:linear-gradient(100deg,#0b0d12 0%,#1a1d24 40%,#4a4f58 60%,#8e96a2 80%,#c9cfd6 100%)}
.hero-arrow{top:390px;width:20px;height:30px}
.hero-title{left:78px;top:330px;font-family:'Roboto Condensed',Arial,sans-serif;font-style:italic;font-size:58px;color:var(--red);letter-spacing:1px}
.hero-sub{left:78px;top:398px;width:560px;font-style:italic;font-size:24px;line-height:30px;color:var(--white)}
.btn{display:flex;align-items:center;justify-content:center;border-radius:26px;font-size:19px;text-transform:uppercase;letter-spacing:.3px}
.btn-white{background:var(--white);color:var(--ink)}
.btn-red{background:var(--red);color:var(--white)}

/* headings */
.h-section{left:0;width:1200px;text-align:center;font-size:44px;font-weight:400;color:var(--ink);letter-spacing:.5px}
.h-section span{color:var(--red)}
.lead{left:154px;width:895px;text-align:center;font-size:14px;line-height:23px;color:var(--muted)}

/* service cards */
.card{background:var(--white);border:1px solid var(--line);box-shadow:0 2px 6px rgba(0,0,0,.06)}
.card-title{position:absolute;left:0;width:100%;text-align:center;font-size:22px;color:var(--red);text-transform:uppercase}
.card-text{position:absolute;left:24px;width:282px;text-align:center;font-size:14px;line-height:22px;color:var(--muted)}
.card-featured{border:2px solid var(--red)}

/* why choose */
.why{left:0;top:1393px;width:1200px;height:565px;background:linear-gradient(180deg,#e9e9e9,#f7f7f7 50%,#e6e6e6)}
.why-icon{width:90px;height:90px;border-radius:50%;background:var(--red);display:flex;align-items:center;justify-content:center}
.why-title{font-size:20px;color:var(--ink)}
.why-text{font-size:14px;line-height:22px;color:var(--muted);width:270px}
.why-right .why-title,.why-right .why-text{text-align:right}

/* band */
.band-left{left:0;top:1958px;width:601px;height:154px;background:var(--charcoal)}
.band-right{left:601px;top:1958px;width:599px;height:154px;background:var(--red)}
.band-title{font-size:38px;color:var(--white);font-weight:300;letter-spacing:.5px}
.band-sub{font-size:16px;color:var(--white)}

/* about */
.about-title{left:78px;top:2166px;font-size:44px;color:var(--ink)}
.about-title span{color:var(--red)}
.about-sub{left:78px;top:2220px;font-size:17px;color:var(--ink)}
.about-text{left:78px;top:2250px;width:560px;font-size:14px;line-height:22px;color:var(--muted)}
.about-text p{margin-bottom:6px}

/* works */
.works{left:0;top:2531px;width:1200px;height:579px;background:var(--panel)}
.work{background:var(--white);box-shadow:0 2px 6px rgba(0,0,0,.08)}
.work-logo{position:absolute;left:0;top:0;width:100%;height:50px;display:flex;align-items:center;justify-content:center;font-size:22px;font-weight:700;color:var(--ink)}
.work-photo{position:absolute;left:0;top:50px;width:100%;height:123px}
.work-name{position:absolute;left:14px;top:188px;font-size:15px;color:var(--red)}
.work-place{position:absolute;left:14px;top:211px;font-size:15px;color:var(--ink)}
.work-text{position:absolute;left:14px;top:238px;width:222px;font-size:13px;line-height:20px;color:var(--muted)}

/* contact */
.field{background:var(--white);border:1px solid #dcdcdc;font-size:14px;color:#999;padding:14px 16px}
.c-line{font-size:14px;color:var(--muted);display:flex;gap:16px;align-items:flex-start;line-height:22px}

/* clients */
.clients{left:0;top:3768px;width:1200px;height:162px;background:var(--red)}
.client{background:var(--white);display:flex;align-items:center;justify-content:center;font-size:20px;font-weight:700;color:var(--ink);text-align:center}

/* footer */
.footer{left:0;top:3930px;width:1200px;height:266px;background:var(--footer)}
.f-icon{width:94px;height:94px;border-radius:50%;border:2px solid var(--red-dark);display:flex;align-items:center;justify-content:center}
.f-text{font-size:15px;color:#cfd0d3;text-align:center;width:360px}
.social{width:48px;height:48px;background:#3d4048}
.social.first{background:#3b5ba4}
.copy{left:0;top:4150px;width:1200px;text-align:center;font-size:14px;color:#a9abb0}
.copy span{color:var(--red)}
</style>
</head>
<body>

<!-- header -->
<div class="abs topline"></div>
<div class="abs brand"><div class="brand-dot"></div><div class="brand-name">VARNO</div></div>
<nav class="abs nav">
  <a class="active" href="#">Home</a>
  <a href="#">Varno Story</a>
  <a href="#">Our Work</a>
  <a href="#">Electrical</a>
  <a href="#">LED Lighting</a>
  <a href="#">Solar Power</a>
  <a href="#">Contact Us</a>
</nav>

<!-- hero -->
<div class="ph hero" role="img" aria-label="Electrician wiring a switchboard beside night city lights and rooftop solar panels"></div>
<svg class="abs hero-arrow" style="left:30px" viewBox="0 0 20 30"><path d="M14 6 L6 15 L14 24" fill="none" stroke="#ccc" stroke-width="3"/></svg>
<div class="abs hero-title">SPARK EVERY DAY</div>
<div class="abs hero-sub">Australia's largest fully integrated electrical &amp; Energy Solutions provider.</div>
<div class="abs btn btn-white" style="left:78px;top:475px;width:168px;height:48px">Know More</div>
<div class="abs btn btn-red" style="left:266px;top:475px;width:173px;height:48px">Contact Us</div>

<!-- welcome -->
<h1 class="abs h-section" style="top:732px">WELCOME TO <span>VARNO</span></h1>
<p class="abs lead" style="top:792px">Varno Electrical was formed to be an expert Electricity Contracting Company providing services to all Residential and Commercial Customers. With over 10 years of experience, Varno Electrical has developed a highly-experienced team of professionals that ensure all our customer expectations are met.</p>

<div class="abs card" style="left:78px;top:912px;width:330px;height:416px">
  <div class="ph" style="left:0;top:0;width:100%;height:207px;background:linear-gradient(135deg,#d9dde2,#8a9099)" role="img" aria-label="Electrician working on a switchboard"></div>
  <div class="card-title" style="top:240px">Electrical</div>
  <div class="card-text" style="top:298px">Melbourne wide , Quick Response time , Electrical Services provide by experienced electricians</div>
</div>
<div class="abs card card-featured" style="left:434px;top:912px;width:330px;height:416px">
  <div class="card-title" style="top:40px">LED Lighting</div>
  <div class="card-text" style="top:92px">Melbourne wide , Quick Response time , Electrical Services provide by experienced electricians</div>
  <div class="ph" style="left:0;top:207px;width:100%;height:207px;background:linear-gradient(180deg,#cfd3d8,#6e747c)" role="img" aria-label="Commercial warehouse lit by LED fittings"></div>
  <svg class="abs" style="right:0;bottom:0" width="50" height="50" viewBox="0 0 50 50"><path d="M50 0 L50 50 L0 50 Z" fill="var(--red)"/><path d="M30 28 L37 35 L30 42" fill="none" stroke="#fff" stroke-width="3"/></svg>
</div>
<div class="abs card" style="left:789px;top:912px;width:333px;height:416px">
  <div class="ph" style="left:0;top:0;width:100%;height:207px;background:linear-gradient(160deg,#7fb0df,#2c4e82)" role="img" aria-label="Technician installing rooftop solar panels"></div>
  <div class="card-title" style="top:240px">Solar Power</div>
  <div class="card-text" style="top:298px">Melbourne wide , Quick Response time , Electrical Services provide by experienced electricians</div>
</div>

<!-- why choose us -->
<div class="abs why"></div>
<h2 class="abs h-section" style="top:1440px">WHY CHOOSE <span>US</span></h2>
<div class="ph" style="left:517px;top:1510px;width:238px;height:448px;background:radial-gradient(ellipse at 50% 30%,#f3b35c 0%,#e9d7c2 35%,rgba(233,215,195,0) 70%)" role="img" aria-label="Hand touching a satisfaction guaranteed badge"></div>

<div class="abs why-icon" style="left:78px;top:1555px"><svg width="44" height="44" viewBox="0 0 44 44"><path d="M8 23 L18 32 L36 12" fill="none" stroke="#fff" stroke-width="4"/></svg></div>
<div class="abs" style="left:201px;top:1562px"><div class="why-title">Professional service</div><div class="why-text">When you hire a Varno Electrical Electrician you will get a professional.. &rsaquo;</div></div>
<div class="abs why-icon" style="left:78px;top:1675px"><svg width="44" height="44" viewBox="0 0 44 44"><path d="M22 6 L26.7 16 L38 17.2 L29.6 24.8 L32 36 L22 30.3 L12 36 L14.4 24.8 L6 17.2 L17.3 16 Z" fill="#fff"/></svg></div>
<div class="abs" style="left:201px;top:1684px"><div class="why-title">5 year workmanship guarantee</div><div class="why-text">You can buy with confidence as all of our work has a 5 year workmanship guarantee.. &rsaquo;</div></div>
<div class="abs why-icon" style="left:78px;top:1807px"><svg width="44" height="44" viewBox="0 0 44 44"><circle cx="22" cy="22" r="13" fill="none" stroke="#fff" stroke-width="4" stroke-dasharray="22 6"/></svg></div>
<div class="abs" style="left:201px;top:1816px"><div class="why-title">Environmentally friendly</div><div class="why-text">We a committed to reducing carbon emissions by installing Solar.. &rsaquo;</div></div>

<div class="abs why-right" style="left:731px;top:1562px"><div class="why-title">Fully insured</div><div class="why-text">Fully insured &amp; equipped to handle break downs &amp; service call outs.. &rsaquo;</div></div>
<div class="abs why-icon" style="left:1026px;top:1555px"><svg width="44" height="44" viewBox="0 0 44 44"><path d="M22 6 L36 11 L36 22 C36 30 30 36 22 39 C14 36 8 30 8 22 L8 11 Z" fill="none" stroke="#fff" stroke-width="3.5"/></svg></div>
<div class="abs why-right" style="left:731px;top:1690px"><div class="why-title">Value for Money</div><div class="why-text">We provide extremely competitive pricing, which means you get value for.. &rsaquo;</div></div>
<div class="abs why-icon" style="left:1026px;top:1683px"><svg width="44" height="44" viewBox="0 0 44 44"><text x="22" y="32" text-anchor="middle" font-family="Roboto,Arial,sans-serif" font-size="30" font-weight="700" fill="#fff">$</text></svg></div>

<!-- band -->
<div class="abs band-left"></div>
<div class="abs band-right"></div>
<div class="abs band-title" style="left:78px;top:2004px">VARNO BRAND <span style="color:var(--red)">MUSIC</span></div>
<div class="abs band-sub" style="left:78px;top:2054px">What Does your brand sound like ? <span style="color:var(--red)">&rsaquo;</span></div>
<div class="abs band-title" style="left:666px;top:2004px">VARNO <span style="font-weight:500">STORY</span></div>
<div class="abs band-sub" style="left:666px;top:2054px">Electrical and Energy Solutions are at the forefront. &rsaquo;</div>

<!-- about -->
<h2 class="abs about-title">ABOUT <span>VARNO</span></h2>
<div class="abs about-sub">Spark Every Day.</div>
<div class="abs about-text">
  <p>Varno Electrical was formed to be an expert Electricity Contracting Company providing services to all Residential and Commercial Customers. With over 10 years of experience, Varno Electrical has developed a highly-experienced team of professionals that ensure all our customer expectations are met.</p>
  <p>Varno Electrical was formed to be an expert Electricity Contracting Company providing services to all Residential and Commercial Customers.</p>
</div>
<div class="abs btn btn-red" style="left:78px;top:2414px;width:177px;height:53px">Know More</div>
<div class="ph" style="left:685px;top:2176px;width:437px;height:291px;background:linear-gradient(135deg,#e6e8eb,#9aa1aa)" role="img" aria-label="Video still of an electrician working at a switchboard"></div>
<svg class="abs" style="left:864px;top:2290px" width="72" height="52" viewBox="0 0 72 52"><rect width="72" height="52" rx="12" fill="var(--red)"/><path d="M28 14 L50 26 L28 38 Z" fill="#fff"/></svg>

<!-- works -->
<div class="abs works"></div>
<h2 class="abs h-section" style="top:2584px">OUR <span>WORKS</span></h2>

<div class="abs work" style="left:78px;top:2663px;width:249px;height:358px">
  <div class="work-logo">Harwell Signs</div>
  <div class="ph work-photo" style="background:linear-gradient(180deg,#b9bec4,#5d636a)" role="img" aria-label="Sign workshop interior"></div>
  <div class="work-name">- Marco T.</div><div class="work-place">Mount Waverley VIC</div>
  <div class="work-text">I found Ethan to be well organised, punctual, professional and a good communicator. He did the job at a very ..</div>
</div>
<div class="abs work" style="left:344px;top:2663px;width:249px;height:358px">
  <div class="work-logo">Norvik Steel</div>
  <div class="ph work-photo" style="background:linear-gradient(180deg,#c5c9ce,#6a7079)" role="img" aria-label="Steel warehouse interior"></div>
  <div class="work-name">- Pellan</div><div class="work-place">Cranbourne North VIC</div>
  <div class="work-text">Excellent work and very professional. Ethan takes time to explain everything &amp; demonstrate workings. Very clear.</div>
</div>
<div class="abs work" style="left:607px;top:2663px;width:249px;height:358px">
  <div class="work-logo">Outback Supply Co</div>
  <div class="ph work-photo" style="background:linear-gradient(180deg,#d0c7b6,#7b6f5c)" role="img" aria-label="Retail store interior with LED lighting"></div>
  <div class="work-name">- Liam Crossley</div><div class="work-place">Executive Outback Supply Co</div>
  <div class="work-text">Outback Supply Co have recently had their lights upgraded to LED lighting at our Head office and the majority of our retail stores.</div>
</div>
<div class="abs work" style="left:873px;top:2663px;width:249px;height:358px">
  <div class="work-logo" style="color:var(--red)">Velvetia</div>
  <div class="ph work-photo" style="background:linear-gradient(180deg,#cbb8bb,#6e5a5e)" role="img" aria-label="Shop interior after lighting upgrade"></div>
  <div class="work-name">- D. Fenwick</div><div class="work-place">Balwyn North, VIC</div>
  <div class="work-text">They clean up after the job, explain ed everything I needed to know and answered all questions, very professional.</div>
</div>
<div class="abs btn btn-red" style="left:523px;top:3040px;width:154px;height:53px">View All</div>

<!-- contact -->
<h2 class="abs h-section" style="top:3212px">CONTACT <span>US</span></h2>
<p class="abs lead" style="top:3278px">Lorem Ipsum is simply dummy text of the printing and typesetting industry. Lorem Ipsum has been the industry's standard dummy text ever since the 1500s, when an unknown printer took.</p>
<div class="ph" style="left:78px;top:3330px;width:520px;height:350px;background:radial-gradient(ellipse at 60% 50%,#f1f1f1,rgba(255,255,255,0) 70%)" role="img" aria-label="Faint world map background"></div>
<div class="abs brand" style="top:3340px"><div class="brand-dot"></div><div class="brand-name">VARNO</div></div>
<p class="abs" style="left:78px;top:3430px;width:540px;font-size:14px;line-height:22px;color:var(--muted)">Varno Electrical was formed to be an expert Electricity Contracting Company providing services to all Residential and Commercial Customers. With over 10 years of experience, Varno Electrical has developed a highly-experienced team of professionals that ensure all.</p>
<div class="abs c-line" style="left:78px;top:3560px"><svg width="18" height="20" viewBox="0 0 18 20"><path d="M9 1 C4.5 1 2 4 2 7.5 C2 12 9 19 9 19 C9 19 16 12 16 7.5 C16 4 13.5 1 9 1 Z" fill="none" stroke="var(--red)" stroke-width="2"/></svg><span>12/84 Wexley Rd Mount Waverley<br>VIC 3149</span></div>
<div class="abs c-line" style="left:78px;top:3614px"><svg width="18" height="20" viewBox="0 0 18 20"><path d="M4 2 L7 2 L8.5 6 L6.5 7.5 C7.5 10 9 11.5 11.5 12.5 L13 10.5 L17 12 L17 15 C17 16 16 17 15 17 C8 17 2 11 2 4 C2 3 3 2 4 2 Z" fill="var(--red)"/></svg><span>134 209</span></div>
<div class="abs c-line" style="left:78px;top:3655px"><svg width="18" height="20" viewBox="0 0 18 20"><rect x="1" y="4" width="16" height="12" fill="none" stroke="var(--red)" stroke-width="2"/><path d="M1 4 L9 11 L17 4" fill="none" stroke="var(--red)" stroke-width="2"/></svg><span>service@varnoelectrical-example.com.au</span></div>

<div class="abs field" style="left:624px;top:3354px;width:498px;height:50px">Name</div>
<div class="abs field" style="left:624px;top:3416px;width:498px;height:50px">E-Mail Address</div>
<div class="abs field" style="left:624px;top:3477px;width:240px;height:50px">Phone</div>
<div class="abs field" style="left:882px;top:3477px;width:240px;height:50px">Company</div>
<div class="abs field" style="left:624px;top:3541px;width:498px;height:95px">Message</div>
<div class="abs btn btn-red" style="left:624px;top:3653px;width:498px;height:50px;font-size:20px">Submit</div>

<!-- clients -->
<div class="abs clients"></div>
<div class="abs client" style="left:204px;top:3796px;width:176px;height:97px">Velvetia</div>
<div class="abs client" style="left:417px;top:3796px;width:165px;height:97px">Heron Plumbing</div>
<div class="abs client" style="left:621px;top:3796px;width:165px;height:97px">Golden Grill</div>
<div class="abs client" style="left:828px;top:3796px;width:165px;height:97px">Outback Supply Co</div>

<!-- footer -->
<div class="abs footer"></div>
<div class="abs f-icon" style="left:196px;top:3950px"><svg width="36" height="36" viewBox="0 0 36 36"><path d="M4 18 L18 5 L32 18 M8 15 L8 31 L15 31 L15 22 L21 22 L21 31 L28 31 L28 15" fill="none" stroke="var(--red)" stroke-width="3"/></svg></div>
<div class="abs f-icon" style="left:552px;top:3950px"><svg width="36" height="36" viewBox="0 0 20 20"><path d="M4 2 L7 2 L8.5 6 L6.5 7.5 C7.5 10 9 11.5 11.5 12.5 L13 10.5 L17 12 L17 15 C17 16 16 17 15 17 C8 17 2 11 2 4 C2 3 3 2 4 2 Z" fill="var(--red)"/></svg></div>
<div class="abs f-icon" style="left:910px;top:3950px"><svg width="36" height="36" viewBox="0 0 18 20"><rect x="1" y="4" width="16" height="12" fill="none" stroke="var(--red)" stroke-width="2"/><path d="M1 4 L9 11 L17 4" fill="none" stroke="var(--red)" stroke-width="2"/></svg></div>
<div class="abs f-text" style="left:63px;top:4026px">254, Office area name,City,Country</div>
<div class="abs f-text" style="left:419px;top:4026px">+61 3 9012 3456</div>
<div class="abs f-text" style="left:777px;top:4026px">info@northlane-example.com</div>
<div class="abs social first" style="left:513px;top:4065px"></div>
<div class="abs social" style="left:576px;top:4065px"></div>
<div class="abs social" style="left:639px;top:4065px"></div>
<div class="abs copy">&copy;<span>VARNO SPARK EVERY DAY</span> - 2017. All Rights Reserved. | Terms and Conditions Privacy</div>

</body>
</html>
```